Multi-Line Insurance PPC Landing Page - Conversion optimized.

We have a PPC landing page used for the general population to get an insurance quote through an agent's site.

We'd like to improve the page for PPC traffic, make it more conversion friendly.

Site should be a single long page.

We will dynamically change the form and headlines on the page depending on what insurance "line" is being called. ie, Lift, Auto, Home, Business.

The enclosed AI file has all of the raw elements we need. We're looking to enhance the design and conversion ability.

Target Market(s)

General public needed insurance services.

Industry/Entity Type

Insurance Broker

Number of Pages Required

1 page

Font styles to use
Sans Serif

Requirements
Must have
• Form, agent picture, name, address.

```html
<!DOCTYPE html>
<html lang="en">
<head>
<meta charset="utf-8">
<title>Insurance Agent – Get a Quote</title>
<link href="https://fonts.googleapis.com/css2?family=Open+Sans:wght@400;600;700;800&display=swap" rel="stylesheet">
<style>
:root{
  --blue:#1f5fae;
  --blue-dark:#163f73;
  --navy:#102a4c;
  --green:#3a8f1e;
  --green-light:#56ad2c;
  --gray-bg:#eeeeee;
  --panel:#f6f6f6;
  --line:#cfcfcf;
  --text:#555;
  --head:#2b2b2b;
  --white:#fff;
}
*{box-sizing:border-box;margin:0;padding:0}
html,body{width:1200px;height:2992px;overflow:hidden}
body{font-family:"Open Sans",Arial,sans-serif;color:var(--text);background:var(--white);position:relative}
section,header,footer{position:absolute;left:0;width:1200px}

/* header */
.site-header{top:0;height:96px;background:var(--white);box-shadow:0 2px 6px rgba(0,0,0,.15);z-index:2}
.brand{position:absolute;left:0;top:0;height:72px;width:330px;background:var(--blue);clip-path:polygon(0 0,100% 0,86% 100%,0 100%);color:var(--white);font-weight:700;font-size:30px;line-height:72px;padding-left:40px}
.header-call{position:absolute;right:40px;top:14px;display:flex;align-items:center;gap:12px}
.header-call .label{font-size:14px;color:var(--text)}
.header-call .num{font-size:28px;font-weight:700;color:var(--head);line-height:1.1}

/* hero */
.hero{top:96px;height:560px}
.hero-photo{position:absolute;inset:0;background:linear-gradient(100deg,#c9b49a 0%,#8c7a5f 30%,#7f9a88 55%,#a9b7bf 75%,#5e8a3c 100%)}
.hero-title{position:absolute;right:70px;top:380px;color:var(--white);font-size:58px;font-weight:700;text-shadow:0 2px 6px rgba(0,0,0,.4)}
.btn-blue{display:inline-block;background:var(--blue);color:var(--white);font-weight:700;border-radius:4px}
.hero .btn-blue{position:absolute;right:150px;top:470px;font-size:24px;padding:16px 30px}

/* quote */
.quote{top:656px;height:424px;background:var(--gray-bg)}
.agent-card{position:absolute;left:80px;top:22px;width:300px;height:380px;background:var(--white);border:1px solid var(--line);text-align:center;padding-top:20px}
.agent-photo{width:190px;height:190px;border-radius:50%;margin:0 auto;border:6px solid var(--blue);background:linear-gradient(160deg,#dfe6ee,#7c8ea6)}
.agent-name{margin-top:22px;font-size:22px;font-weight:700;color:var(--head)}
.agent-phone{margin-top:8px;font-size:17px;font-weight:700;color:var(--head);display:flex;justify-content:center;align-items:center;gap:8px}
.agent-address{margin-top:10px;font-size:15px;font-weight:600;color:var(--head);line-height:1.4}
.quote-form{position:absolute;left:420px;top:22px;width:700px}
.quote-form h2{font-size:28px;font-weight:400;color:var(--head);margin-bottom:18px}
.quote-form h2 strong{color:var(--blue)}
.fields{display:grid;grid-template-columns:1fr 1fr;column-gap:40px;row-gap:14px}
.field label{display:block;font-size:13px;font-weight:600;color:var(--head);margin-bottom:4px}
.input{height:30px;background:var(--white);border:1px solid var(--line);font-size:12px;color:#999;padding:6px 8px}
.dob{display:flex;gap:8px}.dob .input{flex:1}
.btn-green{display:inline-block;background:var(--green);color:var(--white);font-weight:700;border-radius:3px}
.quote-form .btn-green{margin-top:16px;font-size:15px;padding:8px 26px}

/* section titles */
.section-title{text-align:center;font-size:32px;font-weight:700;color:var(--blue);display:flex;align-items:center;justify-content:center;gap:20px}
.section-title::before,.section-title::after{content:"";width:200px;height:1px;background:var(--line)}
.section-title span{color:var(--head)}

.about{top:1080px;height:200px;padding:28px 100px 0}
.about p{margin-top:20px;font-size:16px;line-height:1.6;text-align:center}

/* products */
.products{top:1280px;height:1030px;background:var(--panel);padding-top:30px}
.product-grid{position:absolute;left:96px;top:100px;display:grid;grid-template-columns:repeat(3,312px);column-gap:36px;row-gap:36px}
.product-card{height:420px;background:var(--white);box-shadow:0 2px 6px rgba(0,0,0,.15);text-align:center}
.product-head{height:64px;background:var(--blue);color:var(--white);font-size:20px;font-weight:700;line-height:64px;position:relative;border-radius:6px 6px 0 0}
.product-head .badge{position:absolute;left:50%;top:-22px;margin-left:-22px;width:44px;height:44px;border-radius:50%;background:var(--blue);border:3px solid var(--white)}
.product-photo{height:140px}
.product-card p{font-size:14px;line-height:1.55;padding:18px 22px 0;height:130px}
.product-card .btn-green{font-size:14px;padding:8px 20px}

/* reviews */
.reviews{top:2310px;height:310px;padding-top:36px}
.review{position:absolute;top:120px;width:480px;display:flex;gap:22px}
.review-photo{width:100px;height:100px;border-radius:50%;flex:none;border:4px solid var(--line)}
.review-body p{background:var(--panel);font-size:14px;line-height:1.5;padding:14px 18px}
.review-body .who{margin-top:14px;text-align:center;font-weight:700;color:var(--blue);font-size:15px}

/* companies */
.companies{top:2620px;height:200px;padding-top:20px}
.logo-row{position:absolute;left:60px;right:60px;top:100px;display:flex;align-items:center;justify-content:space-between}
.logo-name{font-size:26px;font-weight:700;color:var(--head)}
.arrow{width:40px;height:40px;background:var(--blue);display:flex;align-items:center;justify-content:center}

/* footer */
.site-footer{top:2820px;height:172px;background:var(--navy);color:#c8d3e2;padding:24px 60px}
.disclaimer h4{color:var(--white);font-size:15px;margin-bottom:6px}
.disclaimer p{font-size:13px;line-height:1.5;width:560px}
.copyright{position:absolute;left:60px;bottom:18px;font-size:12px}
.footer-contact{position:absolute;right:60px;top:24px;text-align:left;color:var(--white)}
.footer-contact .num{font-size:20px;font-weight:700;display:flex;align-items:center;gap:8px}
.footer-contact .addr{font-size:13px;margin-top:6px;padding-left:28px;line-height:1.4}
.footer-brand{position:absolute;right:60px;bottom:14px;font-size:34px;font-weight:700;color:var(--white)}
</style>
</head>
<body>

<header class="site-header">
  <div class="brand">Insurance Agent</div>
  <div class="header-call">
    <svg width="34" height="34" viewBox="0 0 34 34"><circle cx="17" cy="17" r="17" fill="#3a8f1e"/><path d="M12 9l4 4-2 3c1 2 3 4 5 5l3-2 4 4-3 3c-6 0-14-8-14-14z" fill="#fff"/></svg>
    <div><div class="label">Get a quote quote by phone</div><div class="num">(555) 214-7731</div></div>
  </div>
</header>

<section class="hero">
  <div class="hero-photo" role="img" aria-label="Smiling couple outdoors in front of a family house with a green lawn"></div>
  <h1 class="hero-title">Home Insurance</h1>
  <span class="btn-blue">GET A QUOTE!</span>
</section>

<section class="quote">
  <div class="agent-card">
    <div class="agent-photo" role="img" aria-label="Portrait of the insurance agent in a suit"></div>
    <div class="agent-name">Marcus Bell - Agent</div>
    <div class="agent-phone"><svg width="16" height="16" viewBox="0 0 34 34"><path d="M8 4l7 7-3 4c2 3 5 6 8 8l4-3 7 7-4 5C16 32 2 18 3 8z" fill="#1f5fae"/></svg>(555) 214-7730</div>
    <div class="agent-address">2280 Harbor Ave.<br>Fairview, CA 90000</div>
  </div>
  <form class="quote-form">
    <h2><strong>Get An Instant</strong> Insurance Quote.</h2>
    <div class="fields">
      <div class="field"><label>Full Name :</label><div class="input"></div></div>
      <div class="field"><label>Height/Weight :</label><div class="input"></div></div>
      <div class="field"><label>Sex :</label><div class="input">Select</div></div>
      <div class="field"><label>Tobacco Use :</label><div class="input">Select</div></div>
      <div class="field"><label>Date of Birth :</label><div class="dob"><div class="input">Month</div><div class="input">Day</div><div class="input">Year</div></div></div>
      <div class="field"><label>Phone :</label><div class="input"></div></div>
      <div class="field"><label>Current Health :</label><div class="input">Select</div></div>
      <div class="field"><label>Email :</label><div class="input"></div></div>
    </div>
    <span class="btn-green">SUBMIT</span>
  </form>
</section>

<section class="about">
  <h2 class="section-title">About&nbsp;<span>Insurance Agent</span></h2>
  <p>Our local agent helps families and businesses compare coverage from trusted carriers. We review your needs, explain every option in plain language and find a policy that fits your budget. From the first call to the day you file a claim, you work with one person who knows your name and answers quickly whenever you need help with your policy.</p>
</section>

<section class="products">
  <h2 class="section-title">Our&nbsp;<span>Insurance Products</span></h2>
  <div class="product-grid">
    <article class="product-card">
      <div class="product-head"><span class="badge"></span>Auto Insurance</div>
      <div class="product-photo" role="img" aria-label="Hand holding car keys and a toy car" style="background:linear-gradient(135deg,#2b3a52,#7d8ea5)"></div>
      <p>Protect your car and driving record with liability, collision and roadside plans built around how you drive.</p>
      <span class="btn-green">GET A QUOTE!</span>
    </article>
    <article class="product-card">
      <div class="product-head"><span class="badge"></span>Home Insurance</div>
      <div class="product-photo" role="img" aria-label="Hands sheltering a small model house" style="background:linear-gradient(135deg,#f2e1d1,#c0392b)"></div>
      <p>Cover your house, belongings and family against fire, theft and storm damage with flexible home plans.</p>
      <span class="btn-green">GET A QUOTE!</span>
    </article>
    <article class="product-card">
      <div class="product-head"><span class="badge"></span>Life Insurance</div>
      <div class="product-photo" role="img" aria-label="Family playing together on a beach" style="background:linear-gradient(180deg,#a9d3ee,#e8d8b8)"></div>
      <p>Give the people you love lasting security with term and whole life options at affordable monthly rates.</p>
      <span class="btn-green">GET A QUOTE!</span>
    </article>
    <article class="product-card">
      <div class="product-head"><span class="badge"></span>Health Insurance</div>
      <div class="product-photo" role="img" aria-label="Red heartbeat line on a white background" style="background:linear-gradient(135deg,#f7f7f7,#e6b0ac)"></div>
      <p>Find medical plans for individuals and families with trusted doctors, fair deductibles and simple claims.</p>
      <span class="btn-green">GET A QUOTE!</span>
    </article>
    <article class="product-card">
      <div class="product-head"><span class="badge"></span>Business Insurance</div>
      <div class="product-photo" role="img" aria-label="Business team under umbrellas at sunset" style="background:linear-gradient(180deg,#f0a23a,#3a2a1c)"></div>
      <p>Keep your company running with property, liability and workers coverage tailored to your industry and size.</p>
      <span class="btn-green">GET A QUOTE!</span>
    </article>
    <article class="product-card">
      <div class="product-head"><span class="badge"></span>Disability Insurance</div>
      <div class="product-photo" role="img" aria-label="Person in a wheelchair under a blue sky" style="background:linear-gradient(180deg,#3d78c4,#c9d9ea)"></div>
      <p>Replace lost income when injury or illness keeps you from working, so bills stay paid on time.</p>
      <span class="btn-green">GET A QUOTE!</span>
    </article>
  </div>
</section>

<section class="reviews">
  <h2 class="section-title">Our&nbsp;<span>Customer Review</span></h2>
  <div class="review" style="left:90px">
    <div class="review-photo" role="img" aria-label="Customer portrait" style="background:linear-gradient(160deg,#d9d2c8,#6f6a63)"></div>
    <div class="review-body"><p>Switching was easy and I saved on my auto and home policies. Every question got a quick, friendly answer.</p><div class="who">Mr. Alan Preston</div></div>
  </div>
  <div class="review" style="left:630px">
    <div class="review-photo" role="img" aria-label="Customer portrait" style="background:linear-gradient(160deg,#eadccf,#8a6f5a)"></div>
    <div class="review-body"><p>Our agent walked us through life coverage step by step. We finally feel confident about our family plan.</p><div class="who">Miss. Clara Preston</div></div>
  </div>
</section>

<section class="companies">
  <h2 class="section-title"><span>Insurance</span>&nbsp;Company</h2>
  <div class="logo-row">
    <span class="arrow"><svg width="16" height="16" viewBox="0 0 16 16"><path d="M11 2L5 8l6 6" stroke="#fff" stroke-width="3" fill="none"/></svg></span>
    <span class="logo-name">Ledgerly</span>
    <span class="logo-name">Hopline</span>
    <span class="logo-name">Stonefield</span>
    <span class="logo-name">Archway Group</span>
    <span class="logo-name">Tierline Tech</span>
    <span class="arrow"><svg width="16" height="16" viewBox="0 0 16 16"><path d="M5 2l6 6-6 6" stroke="#fff" stroke-width="3" fill="none"/></svg></span>
  </div>
</section>

<footer class="site-footer">
  <div class="disclaimer">
    <h4>Disclaimer</h4>
    <p>Coverage is subject to policy terms, eligibility and underwriting. Quotes are estimates and may change after review by the issuing carrier.</p>
  </div>
  <div class="copyright">© 2016 Insurance Agent. All Rights reserved.</div>
  <div class="footer-contact">
    <div class="num"><svg width="20" height="20" viewBox="0 0 34 34"><path d="M8 4l7 7-3 4c2 3 5 6 8 8l4-3 7 7-4 5C16 32 2 18 3 8z" fill="#fff"/></svg>(555) 214-7730</div>
    <div class="addr">2280 Harbor Ave.<br>Fairview, CA 90000</div>
  </div>
  <div class="footer-brand">Insurance Agent</div>
</footer>

</body>
</html>
```